Volbrey Inc Business Card

Looking to get an updated business card for a Contract Machining company (www.volbreyinc.example) - looking for a clean design the portrays the technical nature of the business - colors can follow the website design and be in any combination that makes sense (red black, white, metallic or silver) - logos attached for use also. Would like space for: Name, title, business phone (555 214-3086), cell phone , website (www.volbreyinc.example) - possibly QR code could be integrated for website (designer choice), business address - 418 Harlow Bend, Brackenfeld, DX 48199 (cards will be for 4 employees, I will either need to modify a template or I can provide individual information)
Target Market(s)
Aerospace, defense and medical device manufacturing companies that need machining
Industry/Entity Type
Machining for aerospace, defense, medical
Contact Information for Business Card
Name, Title, Business Phone, Cell Phone, email, business website and business address
Look and feel

```html
<!DOCTYPE html>
<html lang="en">
<head>
<meta charset="utf-8">
<title>Volbrey Inc Business Card</title>
<link rel="stylesheet" href="https://fonts.googleapis.com/css2?family=Poppins:wght@400;500;700;800&display=swap">
<style>
  :root {
    --bg: #2a2a2c;
    --card-dark: #1d1d1f;
    --red: #b51f24;
    --red-bright: #d8262c;
    --red-deep: #8e1519;
    --white: #ffffff;
    --rule: #7a7a7c;
  }
  * { box-sizing: border-box; margin: 0; padding: 0; }
  html, body { width: 1200px; height: 1108px; overflow: hidden; }
  body {
    background: var(--bg);
    font-family: "Poppins", sans-serif;
    display: flex;
    align-items: center;
    justify-content: center;
    gap: 70px;
  }
  .card {
    width: 420px;
    height: 720px;
    border-radius: 22px;
    overflow: hidden;
    position: relative;
    flex-shrink: 0;
  }
  .card-front {
    background: var(--card-dark);
    color: var(--white);
    display: flex;
    flex-direction: column;
    align-items: center;
    padding-top: 52px;
    text-align: center;
  }
  .brand-disc {
    flex-shrink: 0;
    width: 220px;
    height: 220px;
    border-radius: 50%;
    background: var(--red);
  }
  .brand-name {
    margin-top: 26px;
    font-weight: 800;
    font-size: 54px;
    line-height: 1;
    letter-spacing: 1px;
    color: var(--red);
  }
  .brand-suffix {
    margin-top: 2px;
    font-size: 19px;
    font-weight: 400;
    color: var(--red);
    letter-spacing: 1px;
  }
  .person-name {
    margin-top: 22px;
    font-weight: 700;
    font-size: 24px;
    line-height: 1.3;
    color: var(--red);
    letter-spacing: 0.5px;
  }
  .person-title {
    font-size: 19px;
    font-weight: 400;
    line-height: 1.3;
  }
  .icon-row {
    margin-top: 12px;
    display: flex;
    align-items: center;
    gap: 8px;
  }
  .icon-row .rule { width: 52px; height: 1px; background: var(--rule); }
  .icon {
    width: 30px; height: 30px;
    border-radius: 4px;
    background: var(--red);
    display: flex; align-items: center; justify-content: center;
  }
  .icon svg { width: 18px; height: 18px; fill: var(--white); }
  .contact-list {
    margin-top: 10px;
    list-style: none;
    font-size: 18px;
    line-height: 1.38;
  }
  .contact-list .accent { color: var(--red-bright); }
  .divider {
    width: 280px; height: 1px;
    background: var(--rule);
    margin: 10px 0 8px;
  }
  .address { font-size: 18px; line-height: 1.38; font-style: normal; }
  .card-back { background: var(--red); }
  .back-pattern {
    position: absolute; inset: 0;
    background: linear-gradient(160deg, var(--red-bright) 0%, var(--red) 50%, var(--red-deep) 100%);
  }
  .back-disc {
    position: absolute;
    left: 262px; top: 600px;
    width: 40px; height: 40px;
    border-radius: 50%;
    background: var(--white);
  }
</style>
</head>
<body>
  <section class="card card-front" aria-label="Business card front">
    <div class="brand-disc"></div>
    <div class="brand-name">VOLBREY</div>
    <div class="brand-suffix">INC.</div>
    <h1 class="person-name">DANIEL MARSH</h1>
    <p class="person-title">Managing Director</p>
    <div class="icon-row">
      <span class="rule"></span>
      <span class="icon"><svg viewBox="0 0 24 24"><path d="M6.6 10.8a15 15 0 0 0 6.6 6.6l2.2-2.2a1 1 0 0 1 1-.25 11 11 0 0 0 3.6.6 1 1 0 0 1 1 1V20a1 1 0 0 1-1 1A17 17 0 0 1 3 4a1 1 0 0 1 1-1h3.5a1 1 0 0 1 1 1c0 1.25.2 2.45.6 3.6a1 1 0 0 1-.25 1z"/></svg></span>
      <span class="icon"><svg viewBox="0 0 24 24"><path d="M7 2h10a2 2 0 0 1 2 2v16a2 2 0 0 1-2 2H7a2 2 0 0 1-2-2V4a2 2 0 0 1 2-2zm0 3v13h10V5z"/></svg></span>
      <span class="icon"><svg viewBox="0 0 24 24"><path d="M3 5h18v14H3zm2 2v.5l7 5 7-5V7zm0 3v7h14v-7l-7 5z"/></svg></span>
      <span class="icon"><svg viewBox="0 0 24 24"><path d="M12 2a10 10 0 1 0 0 20 10 10 0 0 0 0-20zm6.9 9h-3a15 15 0 0 0-1.4-6A8 8 0 0 1 18.9 11zM12 4.1c.9 1.3 1.7 3.5 1.9 6.9h-3.8c.2-3.4 1-5.6 1.9-6.9zM9.5 5a15 15 0 0 0-1.4 6h-3A8 8 0 0 1 9.5 5zM5.1 13h3a15 15 0 0 0 1.4 6A8 8 0 0 1 5.1 13zM12 19.9c-.9-1.3-1.7-3.5-1.9-6.9h3.8c-.2 3.4-1 5.6-1.9 6.9zm2.5-.9a15 15 0 0 0 1.4-6h3a8 8 0 0 1-4.4 6z"/></svg></span>
      <span class="rule"></span>
    </div>
    <ul class="contact-list">
      <li>555 214-3086</li>
      <li>555 387-2291</li>
      <li>hello@volbreyinc.example</li>
      <li>www.<span class="accent">volbreyinc</span>.example</li>
    </ul>
    <div class="divider"></div>
    <address class="address">418 Harlow Bend,<br>Brackenfeld, DX 48199</address>
  </section>

  <section class="card card-back" aria-label="Business card back">
    <div class="back-pattern" role="img" aria-label="Repeating embossed pattern of brand marks on red"></div>
    <div class="back-disc"></div>
  </section>
</body>
</html>
```